CrestHornSupply.com

I need a new webdesign for a company in the San Jose/SF Bay area that showcases the financial benefits of buying used band instruments for junior high students.This would be opposed to the current and costly option of renting cheap quality instruments from the 2 or 3 local music stores that charge a monthly fee that over the years charges the buyer 3 or 4x over..
Instruments: focus in on Alto Sax, Trumpet, Flute, Clarinet, Trombone, Tenor Sax, Baritone
Target middle schools are Larkfield Middle School and Maple Middle School in San Jose, CA. Both have award winning band programs.
Files attached may or may not be important.
Tabs Needed and funtional
Contact
Shopping Cart
Select Instrument
Checkout
Add to Cart, etc.
Instuments
quantity, etc.
trade in your instrument/sell your instrument
ability to add or take away new instruments for sale. including pictures
Additional questions or info, feel free to ask
Updates
Hi Designers,
Project Deadline Extended
Reason: In the next week you will be receiving specific content that will be required to be had on the website.
New desigins are still welcome. Please continue to contact me if you have questions about your individual designs.
Thanks!
Crest Horn

```html
<!DOCTYPE html>
<html lang="en">
<head>
<meta charset="utf-8">
<title>Crest Horn Instruments</title>
<link href="https://fonts.googleapis.com/css2?family=Open+Sans:wght@400;600;700&display=swap" rel="stylesheet">
<style>
:root{
  --red:#e8222b;
  --red-soft:#f24f56;
  --green:#11a52a;
  --green-light:#5cc04a;
  --dark:#1e1e1e;
  --ink:#333;
  --muted:#555;
  --line:#dcdcdc;
  --gold:#d9b25a;
  --page:#f4f4f4;
}
*{box-sizing:border-box;margin:0;padding:0}
html,body{width:1093px;height:1200px;overflow:hidden}
body{font-family:"Open Sans",Arial,sans-serif;color:var(--ink);background:var(--page);position:relative}
.backdrop{position:absolute;left:0;top:0;width:1093px;height:760px;
  background:linear-gradient(180deg,#6b7a6a 0%,#4d6b45 45%,#7fa070 70%,rgba(244,244,244,1) 100%)}
.sheet{position:absolute;left:166px;top:0;width:761px;height:1200px;background:#f7f7f7}
.abs{position:absolute}
/* header */
.header{left:0;top:0;width:761px;height:102px;background:#fff}
.brand{left:16px;top:36px;display:flex;align-items:center;gap:10px}
.brand-dot{width:18px;height:18px;border-radius:50%;background:var(--red)}
.brand-name{font-size:28px;font-weight:700;color:var(--dark);letter-spacing:.5px}
.toplinks{right:22px;top:32px;display:flex;gap:21px;font-size:8px;color:#444;align-items:center}
.toplinks .accent{color:var(--red)}
.cart-badge{position:relative}
.cart-badge span{position:absolute;top:-9px;right:-6px;width:14px;height:14px;border-radius:50%;background:var(--red);color:#fff;font-size:8px;text-align:center;line-height:14px}
.phone{right:16px;top:60px;display:flex;align-items:center;gap:8px;color:var(--green);font-size:16px}
/* nav */
.nav{left:0;top:102px;width:761px;height:31px;background:linear-gradient(#3a3a3a,#111);display:flex}
.nav a{color:#fff;text-decoration:none;font-size:12px;font-weight:600;padding:0 20px;line-height:31px;border-right:1px solid #444}
.nav a:nth-child(1){width:87px}.nav a:nth-child(2){width:96px;padding-left:18px}.nav a:nth-child(3){width:121px}.nav a:nth-child(4){width:101px}
.search{right:9px;top:106px;width:177px;height:22px;background:#fff;border-radius:2px;font-size:8px;color:#999;padding:6px 10px}
.search svg{position:absolute;right:8px;top:5px}
/* slider */
.slider{left:16px;top:152px;width:506px;height:276px;background:#eee}
.slide-img{width:506px;height:231px;background:linear-gradient(120deg,#e9e3d6 0%,#c9a14f 35%,#8b3a14 60%,#e0d7c4 100%)}
.slide-caption{height:45px;background:rgba(255,255,255,.9);font-size:11px;font-weight:600;padding:14px 13px;position:relative}
.slide-arrows{position:absolute;right:10px;top:11px;display:flex;gap:2px}
.slide-arrows span{width:22px;height:22px;background:#555;display:block}
/* promo boxes */
.promo{left:541px;width:202px;height:130px;color:#fff}
.promo .tab{position:absolute;right:0;top:0;width:142px;height:48px;padding:10px 10px;text-align:right;font-size:10px;line-height:1.3}
.promo .tab b{display:block;font-size:14px;letter-spacing:.5px}
.promo .body{position:absolute;left:0;top:47px;width:202px;height:83px;padding:32px 14px 0 26px;font-size:7.5px;line-height:1.45}
.promo .icon{position:absolute;left:14px;top:6px;width:34px;height:36px;background:#333;border-radius:4px}
.promo .go{position:absolute;right:0;bottom:0;width:30px;height:18px;background:#fff}
.promo .go svg{position:absolute;left:9px;top:4px}
.red .tab,.red .body{background:linear-gradient(var(--red-soft),var(--red))}
.green .tab,.green .body{background:var(--green)}
.faces{position:absolute;left:78px;top:51px;display:flex;gap:3px}
.faces i{width:17px;height:16px;background:#c9a58a;border:1px solid #fff;display:block}
.red .body{padding-top:30px}
/* section headings */
.heading{height:32px;background:linear-gradient(var(--green-light),var(--green));color:#fff;font-size:13px;font-weight:600;padding:8px 12px;border-bottom:2px solid #0d7d1f}
.panel{background:#fff;border:1px solid var(--line)}
.categories{left:16px;top:508px;width:204px;height:241px;padding:10px 8px}
.categories li{list-style:none;font-size:8.5px;color:#444;line-height:23px}
.categories li::before{content:"»";color:var(--green);margin-right:7px}
/* products */
.card{width:147px;height:245px;background:#fff;border:1px solid var(--line)}
.card .photo{margin:6px auto 0;width:128px;height:124px;border-radius:2px}
.card .stars{position:absolute;left:6px;top:134px;display:flex;gap:1px}
.card h3{position:absolute;left:6px;top:148px;font-size:11.5px;color:var(--red);font-weight:600}
.card p{position:absolute;left:7px;top:165px;width:136px;font-size:7px;color:#444;line-height:1.55}
.card .price{position:absolute;left:8px;top:192px;font-size:11.5px;font-weight:600;color:#222}
.card .actions{position:absolute;left:5px;top:216px;display:flex;gap:4px}
.btn-cart{width:79px;height:19px;background:var(--dark);color:#fff;font-size:7.5px;font-weight:600;display:flex;align-items:center;gap:6px;padding-left:7px;border-radius:2px}
.btn-sq{width:18px;height:18px;border:1px solid #bbb;background:#fff;display:flex;align-items:center;justify-content:center}
.gold-sax{background:linear-gradient(160deg,#fff 20%,#d6b45e 50%,#8b6a2a 70%,#fff 90%)}
.gold-bone{background:linear-gradient(130deg,#fff 15%,#d9bd74 40%,#b89448 60%,#fff 85%)}
.black-clar{background:linear-gradient(150deg,#fff 20%,#222 45%,#555 60%,#fff 85%)}
.gold-bari{background:radial-gradient(circle at 50% 50%,#e5c77b 0%,#c89d3f 45%,#fff 75%)}
.gold-tpt{background:linear-gradient(160deg,#fff 25%,#dcc179 50%,#fff 80%)}
/* news */
.news{left:16px;top:780px;width:204px;height:250px;background:linear-gradient(var(--red-soft),var(--red));color:#fff}
.news .note{position:absolute;left:0;top:0;width:54px;height:46px;background:#fff}
.news .note i{position:absolute;left:14px;top:10px;width:26px;height:28px;background:#222;display:block}
.news .title{position:absolute;right:46px;top:12px;text-align:right;font-size:10px;line-height:1.3}
.news .title b{display:block;font-size:13px}
.news .item{position:absolute;left:21px;width:164px;font-size:7.5px;line-height:1.5}
.news .date{font-style:italic;font-size:8px;margin-bottom:3px}
.news .more{text-align:right;text-decoration:underline;font-style:italic;margin-top:2px}
.news .go{position:absolute;right:0;bottom:0;width:30px;height:20px;background:#fff}
.news .go svg{position:absolute;left:9px;top:5px}
/* footer */
.footer{left:0;top:1072px;width:761px;height:128px;background:#fff;border-top:3px solid #1d2730}
.fcol{position:absolute;top:16px}
.fcol h4{color:var(--red);font-size:13px;font-weight:600;margin-bottom:4px}
.fcol li{list-style:none;font-size:8px;line-height:15px;color:#333}
.fcol li::before{content:"» ";color:var(--green)}
.footer .brand{left:576px;top:38px}
.social{position:absolute;left:662px;top:86px;display:flex;gap:9px}
.social span{width:14px;height:14px;border-radius:50%;background:var(--green);display:block}
</style>
</head>
<body>
<div class="backdrop" role="img" aria-label="Photo of a school marching band performing in a baseball stadium"></div>

<div class="sheet">
  <header class="abs header">
    <div class="abs brand"><span class="brand-dot"></span><span class="brand-name">Crest Horn</span></div>
    <nav class="abs toplinks">
      <span>Wish List (0)</span><span>My Account</span><span>Shopping Cart</span><span>Checkout</span>
      <span class="accent">Login &nbsp;|&nbsp; Register</span>
      <span class="cart-badge"><svg width="22" height="18" viewBox="0 0 22 18"><path d="M1 2h4l3 10h10l3-7H7" fill="none" stroke="#888" stroke-width="2"/><circle cx="9" cy="16" r="1.6" fill="#888"/><circle cx="17" cy="16" r="1.6" fill="#888"/></svg><span>0</span></span>
      <span>$ &#8964;</span>
    </nav>
    <div class="abs phone"><svg width="15" height="15" viewBox="0 0 16 16"><circle cx="8" cy="8" r="7" fill="none" stroke="#e8222b" stroke-width="1.6"/><path d="M5 4.5l1.5-.5 1 2-1 1c.5 1 1.3 1.8 2.3 2.3l1-1 2 1-.5 1.5c-3 .3-6.6-3.3-6.3-6.3z" fill="#e8222b"/></svg>415 555 0182</div>
  </header>

  <nav class="abs nav"><a>Home</a><a>About Us</a><a>Instruments</a><a>Buy /Sell</a><a>Contact Us</a></nav>
  <div class="abs search">Search<svg width="12" height="12" viewBox="0 0 12 12"><circle cx="5" cy="5" r="4" fill="none" stroke="#222" stroke-width="1.6"/><path d="M8 8l3 3" stroke="#222" stroke-width="1.8"/></svg></div>

  <section class="abs slider">
    <div class="slide-img" role="img" aria-label="Close-up photo of a trumpet and violin with bow"></div>
    <div class="slide-caption">Donec arcu dolor, sodales ut lobortis adipiscing, auctor id purus.
      <div class="slide-arrows"><span></span><span></span></div></div>
  </section>

  <aside class="abs promo red" style="top:152px">
    <div class="icon" role="img" aria-label="Electric guitar icon"></div>
    <div class="tab">Music Teachers<b>AVAILABLE</b></div>
    <div class="body">Nulla egestas mi non pulvinar sodales. Vesti bulum id luctus augue. Integer sem nisl, susc ipit sit amet cursus non, venenatis</div>
    <div class="faces" role="img" aria-label="Small portraits of music teachers"><i></i><i></i><i></i><i></i><i></i></div>
    <div class="go"><svg width="12" height="10" viewBox="0 0 12 10"><path d="M0 3h6V0l6 5-6 5V7H0z" fill="#e8222b"/></svg></div>
  </aside>
  <aside class="abs promo green" style="top:299px">
    <div class="icon" role="img" aria-label="Microphone icon" style="background:transparent;border:2px solid #222"></div>
    <div class="tab">Music Products<b>HIGHLIGHTS</b></div>
    <div class="body">Nulla egestas mi non pulvinar sodales. Vesti bulum id luctus augue. Integer sem nisl, susc ipit sit amet cursus non, venenatis Praesent aliquet mauris ante,</div>
    <div class="go"><svg width="12" height="10" viewBox="0 0 12 10"><path d="M0 3h6V0l6 5-6 5V7H0z" fill="#e8222b"/></svg></div>
  </aside>

  <h2 class="abs heading" style="left:16px;top:453px;width:204px">CATEGORIES</h2>
  <h2 class="abs heading" style="left:260px;top:453px;width:485px">FEATURED PRODUCTS</h2>

  <ul class="abs panel categories">
    <li>Praesent eget purus eu</li><li>massa rutrum blandit. In viverra,</li><li>augue vitae facilisis hendrerit,</li>
    <li>mauris sem suscipit nisi, et rutrum nibh</li><li>quam at felis. Mauris viverra at</li><li>mauris sed malesuada</li>
    <li>Phasellus augue urna, tristique et</li><li>porta eget, rhoncus at diam Suspendisse</li><li>mollis enim nec lorem consectetu</li>
  </ul>

  <svg width="0" height="0" style="position:absolute">
    <defs>
      <symbol id="star-full" viewBox="0 0 10 10"><path d="M5 .5l1.3 3 3.2.3-2.4 2.1.7 3.2L5 7.4 2.2 9.1l.7-3.2L.5 3.8l3.2-.3z" fill="#f3a712"/></symbol>
      <symbol id="star-empty" viewBox="0 0 10 10"><path d="M5 .5l1.3 3 3.2.3-2.4 2.1.7 3.2L5 7.4 2.2 9.1l.7-3.2L.5 3.8l3.2-.3z" fill="none" stroke="#f3a712" stroke-width=".8"/></symbol>
      <symbol id="cart" viewBox="0 0 14 11"><path d="M0 1h3l2 6h7l2-5H4" fill="none" stroke="#e8222b" stroke-width="1.5"/><circle cx="6" cy="9.5" r="1" fill="#e8222b"/><circle cx="11" cy="9.5" r="1" fill="#e8222b"/></symbol>
      <symbol id="bars" viewBox="0 0 10 8"><path d="M1 7v-1M3 7V5M5 7V3M7 7V2M9 7V0" stroke="#11a52a" stroke-width="1.2"/></symbol>
      <symbol id="fav" viewBox="0 0 10 10"><path d="M5 .5l1.3 3 3.2.3-2.4 2.1.7 3.2L5 7.4 2.2 9.1l.7-3.2L.5 3.8l3.2-.3z" fill="none" stroke="#11a52a" stroke-width=".9"/></symbol>
    </defs>
  </svg>

  <!-- product cards -->
  <article class="abs card" style="left:263px;top:505px">
    <div class="photo gold-sax" role="img" aria-label="Photo of an alto saxophone"></div>
    <div class="stars"><svg width="10" height="10"><use href="#star-full"/></svg><svg width="10" height="10"><use href="#star-full"/></svg><svg width="10" height="10"><use href="#star-full"/></svg><svg width="10" height="10"><use href="#star-empty"/></svg><svg width="10" height="10"><use href="#star-empty"/></svg></div>
    <h3>Alto Sax</h3><p>vitae adipiscing urna accumsan vitae. Nunc varius nunc ut nisl</p><div class="price">$249.99</div>
    <div class="actions"><div class="btn-cart"><svg width="14" height="11"><use href="#cart"/></svg>Add to Cart</div><div class="btn-sq"><svg width="10" height="8"><use href="#bars"/></svg></div><div class="btn-sq"><svg width="10" height="10"><use href="#fav"/></svg></div></div>
  </article>
  <article class="abs card" style="left:431px;top:505px">
    <div class="photo gold-bone" role="img" aria-label="Photo of a trombone"></div>
    <div class="stars"><svg width="10" height="10"><use href="#star-full"/></svg><svg width="10" height="10"><use href="#star-full"/></svg><svg width="10" height="10"><use href="#star-full"/></svg><svg width="10" height="10"><use href="#star-empty"/></svg><svg width="10" height="10"><use href="#star-empty"/></svg></div>
    <h3>Trombone</h3><p>vitae adipiscing urna accumsan vitae. Nunc varius nunc ut nisl</p><div class="price">$249.99</div>
    <div class="actions"><div class="btn-cart"><svg width="14" height="11"><use href="#cart"/></svg>Add to Cart</div><div class="btn-sq"><svg width="10" height="8"><use href="#bars"/></svg></div><div class="btn-sq"><svg width="10" height="10"><use href="#fav"/></svg></div></div>
  </article>
  <article class="abs card" style="left:599px;top:505px">
    <div class="photo black-clar" role="img" aria-label="Photo of a clarinet"></div>
    <div class="stars"><svg width="10" height="10"><use href="#star-full"/></svg><svg width="10" height="10"><use href="#star-full"/></svg><svg width="10" height="10"><use href="#star-full"/></svg><svg width="10" height="10"><use href="#star-empty"/></svg><svg width="10" height="10"><use href="#star-empty"/></svg></div>
    <h3>Clarinet</h3><p>vitae adipiscing urna accumsan vitae. Nunc varius nunc ut nisl</p><div class="price">$249.99</div>
    <div class="actions"><div class="btn-cart"><svg width="14" height="11"><use href="#cart"/></svg>Add to Cart</div><div class="btn-sq"><svg width="10" height="8"><use href="#bars"/></svg></div><div class="btn-sq"><svg width="10" height="10"><use href="#fav"/></svg></div></div>
  </article>
  <article class="abs card" style="left:263px;top:786px">
    <div class="photo gold-bari" role="img" aria-label="Photo of a baritone horn"></div>
    <div class="stars"><svg width="10" height="10"><use href="#star-full"/></svg><svg width="10" height="10"><use href="#star-full"/></svg><svg width="10" height="10"><use href="#star-full"/></svg><svg width="10" height="10"><use href="#star-empty"/></svg><svg width="10" height="10"><use href="#star-empty"/></svg></div>
    <h3>Baritone</h3><p>vitae adipiscing urna accumsan vitae. Nunc varius nunc ut nisl</p><div class="price">$249.99</div>
    <div class="actions"><div class="btn-cart"><svg width="14" height="11"><use href="#cart"/></svg>Add to Cart</div><div class="btn-sq"><svg width="10" height="8"><use href="#bars"/></svg></div><div class="btn-sq"><svg width="10" height="10"><use href="#fav"/></svg></div></div>
  </article>
  <article class="abs card" style="left:431px;top:786px">
    <div class="photo gold-tpt" role="img" aria-label="Photo of a trumpet"></div>
    <div class="stars"><svg width="10" height="10"><use href="#star-full"/></svg><svg width="10" height="10"><use href="#star-full"/></svg><svg width="10" height="10"><use href="#star-full"/></svg><svg width="10" height="10"><use href="#star-empty"/></svg><svg width="10" height="10"><use href="#star-empty"/></svg></div>
    <h3>Trumpet</h3><p>vitae adipiscing urna accumsan vitae. Nunc varius nunc ut nisl</p><div class="price">$249.99</div>
    <div class="actions"><div class="btn-cart"><svg width="14" height="11"><use href="#cart"/></svg>Add to Cart</div><div class="btn-sq"><svg width="10" height="8"><use href="#bars"/></svg></div><div class="btn-sq"><svg width="10" height="10"><use href="#fav"/></svg></div></div>
  </article>
  <article class="abs card" style="left:599px;top:786px">
    <div class="photo gold-sax" role="img" aria-label="Photo of a tenor saxophone"></div>
    <div class="stars"><svg width="10" height="10"><use href="#star-full"/></svg><svg width="10" height="10"><use href="#star-full"/></svg><svg width="10" height="10"><use href="#star-full"/></svg><svg width="10" height="10"><use href="#star-empty"/></svg><svg width="10" height="10"><use href="#star-empty"/></svg></div>
    <h3>Tenor Sax</h3><p>vitae adipiscing urna accumsan vitae. Nunc varius nunc ut nisl</p><div class="price">$249.99</div>
    <div class="actions"><div class="btn-cart"><svg width="14" height="11"><use href="#cart"/></svg>Add to Cart</div><div class="btn-sq"><svg width="10" height="8"><use href="#bars"/></svg></div><div class="btn-sq"><svg width="10" height="10"><use href="#fav"/></svg></div></div>
  </article>

  <section class="abs news">
    <div class="note"><i role="img" aria-label="Music note icon"></i></div>
    <div class="title">Music News &amp;<b>EVENTS</b></div>
    <div class="item" style="top:62px"><div class="date">23-Jun-2014</div>Nulla egestas mi non pulvinar sodales. Vesti bulum id luctus augue. Integer sem nisl, susc ipit sit amet cursus non, venenatis<div class="more">View detail »</div></div>
    <div class="item" style="top:141px"><div class="date">23-Jun-2014</div>Nulla egestas mi non pulvinar sodales. Vesti bulum id luctus augue. Integer sem nisl, susc ipit sit amet cursus non, venenatis<div class="more">View detail »</div></div>
    <div class="go"><svg width="12" height="10" viewBox="0 0 12 10"><path d="M0 3h6V0l6 5-6 5V7H0z" fill="#e8222b"/></svg></div>
  </section>

  <footer class="abs footer">
    <div class="fcol" style="left:19px"><h4>Information</h4><ul><li>About</li><li>Delivery</li><li>Privacy Policy</li><li>Terms &amp; Conditions</li></ul></div>
    <div class="fcol" style="left:156px"><h4>Customer Service</h4><ul><li>Contact Us</li><li>Returns</li><li>Site Map</li></ul></div>
    <div class="fcol" style="left:326px"><h4>Extras</h4><ul><li>Brands</li><li>Gift Vouchers</li><li>Affiliates</li><li>Specials</li></ul></div>
    <div class="fcol" style="left:448px"><h4>My Account</h4><ul><li>My Account</li><li>Order History</li><li>Wish List</li><li>Newsletter</li></ul></div>
    <div class="abs brand"><span class="brand-dot"></span><span class="brand-name" style="font-size:24px">Crest Horn</span></div>
    <div class="social" aria-label="Social links"><span></span><span></span><span></span><span></span></div>
  </footer>
</div>
</body>
</html>
```